BRIVAN 2026 Flyer for Conference

BRIVAN needs a design for a 1-page flyer that we will hand out at an upcoming event & then later post online as a pdf. There are 3 elements which need to be on the flyer:

1) A logo. This should be prominent on the design (e.g., in the middle). The flyer should use the colors that are in that logo (e.g., for accents, design elements, and/or text; not all of these have to be used):
Dark blue: #185577
Med blue: #327C9A
Teal: #4EB1C2
Light Teal: #9EDBE6

2) The conference theme -- Oceans of Knowledge: Diving into Information Literacy -- should be at the flyer's top.

3) Finally, these six tracks should be listed below the theme and the logo (it's font size should be at least a couple sizes smaller than the size used for the theme):
- Pearls of Pedagogy: Teaching Techniques that Work
- The Depth Gauge: Measuring Instructional Impact
- Techtonic Shifts: Innovation and Educational Technology
- Captain's Log: Navigating Leadership in Library Instruction
- Swimming Together: Collaborating with Others
- The Bermuda Triangle: Exploring (Seemingly) Eternal Challenges

Font styles to use
Sans Serif

Colors
0094D4
00A9DD
6FCCEA
C7EBF8
E9F6FB

Requirements
Must have
• The 3 elements listed in the description: 1) the logo, 2) the text of the theme and 3) the text for the tracks.

```html
<!DOCTYPE html>
<html lang="en">
<head>
<meta charset="utf-8">
<title>BRIVAN 2026 – Oceans of Knowledge</title>
<link href="https://fonts.googleapis.com/css2?family=Montserrat:wght@400;700&family=Poppins:wght@600;700&display=swap" rel="stylesheet">
<style>
  :root {
    --dark-blue: #185577;
    --med-blue: #327C9A;
    --teal: #4EB1C2;
    --light-teal: #9EDBE6;
    --accent: #2AA8E8;
    --ink: #111111;
    --white: #FFFFFF;
    --sky-top: #C9F1EE;
    --sky-mid: #A9E4E6;
    --sea-top: #3FA6C4;
    --sea-mid: #1E86AE;
    --sea-deep: #0F5F8A;
  }
  * { box-sizing: border-box; margin: 0; padding: 0; }
  html, body { width: 927px; height: 1200px; overflow: hidden; }
  body { font-family: "Poppins", sans-serif; background: var(--white); }

  .flyer { position: relative; width: 927px; height: 1200px; overflow: hidden; }

  .ocean-backdrop {
    position: absolute; inset: 0;
    background: linear-gradient(180deg,
      var(--sky-top) 0%,
      var(--sky-mid) 38%,
      #B4E6E8 44%,
      var(--sea-top) 46%,
      var(--sea-mid) 65%,
      var(--sea-deep) 100%);
  }

  .brand {
    position: absolute; top: 120px; left: 0; width: 927px;
    display: flex; align-items: center; justify-content: center; gap: 14px;
  }
  .brand-dot { width: 44px; height: 44px; border-radius: 50%; background: var(--light-teal); }
  .brand-name {
    font-family: "Poppins", sans-serif; font-weight: 700; font-size: 60px;
    color: var(--dark-blue); letter-spacing: 1px; line-height: 1;
  }
  .event-meta {
    position: absolute; top: 205px; left: 0; width: 927px; text-align: center;
    font-family: "Poppins", sans-serif; font-weight: 600; font-size: 18px;
    letter-spacing: 4px; color: var(--teal);
  }

  .theme { position: absolute; top: 330px; left: 0; width: 927px; text-align: center; }
  .theme-title {
    font-family: "Montserrat", sans-serif; font-weight: 700; font-size: 44px;
    color: var(--accent); line-height: 1.1; letter-spacing: 0.5px;
  }
  .theme-subtitle {
    font-family: "Montserrat", sans-serif; font-weight: 400; font-size: 37px;
    color: var(--ink); line-height: 1.3; margin-top: 4px;
  }

  .tracks {
    position: absolute; top: 508px; left: 83px;
    display: grid; grid-template-columns: repeat(3, 223px);
    column-gap: 46px; row-gap: 32px;
  }
  .track-card {
    position: relative; width: 223px; height: 284px;
    background: var(--white); border-radius: 28px; padding: 9px;
    text-align: center;
  }
  .track-photo { width: 205px; height: 157px; border-radius: 24px; }
  .photo-pedagogy { background: linear-gradient(160deg, #3E7E78, #2E5E5A 60%, #C89A4A); }
  .photo-depth { background: linear-gradient(180deg, #DCEFF0, #B9C4C0 50%, #6B5A52); }
  .photo-tech { background: linear-gradient(150deg, #6FA9C0, #2B6F8E 60%, #1E3D52); }
  .photo-captain { background: linear-gradient(160deg, #3E4A4C, #7FA6AA 45%, #B77C5C 70%, #2C2A28); }
  .photo-together { background: linear-gradient(150deg, #5C6468, #9AA3A6 45%, #B79A5C 65%, #3A3A3A); }
  .photo-bermuda { background: linear-gradient(150deg, #B9E0DE, #4E8E8E 45%, #D8693E 70%, #2A5A66); }

  .track-icon {
    position: absolute; left: 50%; top: 136px; transform: translateX(-50%);
    width: 62px; height: 62px; border-radius: 50%;
    background: var(--accent); border: 3px solid var(--white);
    display: flex; align-items: center; justify-content: center;
  }
  .track-icon svg { width: 34px; height: 34px; }

  .track-text { margin-top: 40px; line-height: 20px; font-size: 14.5px; }
  .track-name { display: block; font-weight: 600; color: var(--accent); }
  .track-desc { display: block; font-weight: 600; color: var(--ink); }

  .ref-code {
    position: absolute; right: 18px; bottom: 14px;
    font-family: "Poppins", sans-serif; font-weight: 700; font-size: 13px; color: var(--white);
  }
</style>
</head>
<body>
<main class="flyer">
  <div class="ocean-backdrop" role="img" aria-label="Photo of a calm open ocean beneath a pale aqua sky"></div>

  <header>
    <div class="brand">
      <span class="brand-dot"></span>
      <span class="brand-name">BRIVAN 2026</span>
    </div>
    <p class="event-meta">HARBORTON, VA · MAY 7-9</p>
  </header>

  <section class="theme">
    <h1 class="theme-title">OCEANS OF KNOWLEDGE:</h1>
    <p class="theme-subtitle">DIVING INTO INFORMATION LITERACY</p>
  </section>

  <section class="tracks">
    <article class="track-card">
      <div class="track-photo photo-pedagogy" role="img" aria-label="Light bulb and graduation cap resting on an open book before a chalkboard"></div>
      <div class="track-icon">
        <svg viewBox="0 0 34 34" fill="none" stroke="#fff" stroke-width="2" stroke-linecap="round" stroke-linejoin="round">
          <rect x="14" y="6" width="15" height="22" rx="2"/><path d="M18 6v-2h7v2"/>
          <path d="M17 12l3 3M20 12l-3 3M23 19l3 3M26 19l-3 3M19 21l4-6"/>
          <circle cx="8" cy="9" r="3"/><path d="M4 28V16h8v12M8 16v12"/>
        </svg>
      </div>
      <p class="track-text"><span class="track-name">Pearls of Pedagogy:</span><span class="track-desc">Teaching Techniques<br>that Work</span></p>
    </article>

    <article class="track-card">
      <div class="track-photo photo-depth" role="img" aria-label="Audience seated in a bright lecture hall watching a presentation"></div>
      <div class="track-icon">
        <svg viewBox="0 0 34 34" fill="none" stroke="#fff" stroke-width="2" stroke-linecap="round" stroke-linejoin="round">
          <rect x="12" y="4" width="19" height="14" rx="1"/><circle cx="24" cy="11" r="3"/>
          <circle cx="7" cy="8" r="3"/><path d="M4 22v-8h6l4 3"/>
          <circle cx="20" cy="24" r="2.5"/><circle cx="28" cy="24" r="2.5"/><path d="M16 31a4 4 0 0 1 8 0M24 31a4 4 0 0 1 8 0"/>
        </svg>
      </div>
      <p class="track-text"><span class="track-name">The Depth Gauge:</span><span class="track-desc">Measuring<br>Instructional Impact</span></p>
    </article>

    <article class="track-card">
      <div class="track-photo photo-tech" role="img" aria-label="Hands typing on a laptop under a glowing digital transformation interface"></div>
      <div class="track-icon">
        <svg viewBox="0 0 34 34" fill="none" stroke="#fff" stroke-width="2" stroke-linecap="round" stroke-linejoin="round">
          <path d="M11 22a9 9 0 1 1 12 0v4H11z"/><path d="M12 29h10M14 32h6"/>
          <circle cx="21" cy="12" r="3"/><path d="M14 15h3M14 11l3 1M4 13H1M33 13h-3M6 5l-2-2M28 5l2-2"/>
        </svg>
      </div>
      <p class="track-text"><span class="track-name">Techtonic Shifts:</span><span class="track-desc">Innovation and<br>Educational Technology</span></p>
    </article>

    <article class="track-card">
      <div class="track-photo photo-captain" role="img" aria-label="Close-up of two people shaking hands"></div>
      <div class="track-icon">
        <svg viewBox="0 0 34 34" fill="none" stroke="#fff" stroke-width="2" stroke-linecap="round" stroke-linejoin="round">
          <circle cx="17" cy="17" r="9"/><circle cx="17" cy="17" r="3"/>
          <path d="M17 2v6M17 26v6M2 17h6M26 17h6M6.5 6.5l4 4M23.5 23.5l4 4M27.5 6.5l-4 4M10.5 23.5l-4 4"/>
        </svg>
      </div>
      <p class="track-text"><span class="track-name">Captain's Log:</span><span class="track-desc">Navigating Leadership in<br>Library Instruction</span></p>
    </article>

    <article class="track-card">
      <div class="track-photo photo-together" role="img" aria-label="Many hands fitting metal gears together on a wooden table"></div>
      <div class="track-icon">
        <svg viewBox="0 0 34 34" fill="none" stroke="#fff" stroke-width="2" stroke-linecap="round" stroke-linejoin="round">
          <path d="M5 22l7-7 3 3a2.5 2.5 0 1 0 3-3l-3-3 4-4 3 3a2.5 2.5 0 1 1 3 3l-3 3 3 3-10 10-3-3a2.5 2.5 0 1 0-3-3z"/>
          <path d="M3 31l4-4M27 3l4 4"/>
        </svg>
      </div>
      <p class="track-text"><span class="track-name">Swimming Together:</span><span class="track-desc">Collaborating with<br>Others</span></p>
    </article>

    <article class="track-card">
      <div class="track-photo photo-bermuda" role="img" aria-label="Blurred rows of colourful books on library shelves"></div>
      <div class="track-icon">
        <svg viewBox="0 0 34 34" fill="none" stroke="#fff" stroke-width="2" stroke-linecap="round" stroke-linejoin="round">
          <path d="M17 7L6 26M17 7l11 19M8 28h18"/>
          <circle cx="17" cy="5" r="2.5"/><circle cx="5" cy="28" r="2.5"/><circle cx="29" cy="28" r="2.5"/>
        </svg>
      </div>
      <p class="track-text"><span class="track-name">The Bermuda Triangle:</span><span class="track-desc">Exploring (Seemingly)<br>Eternal Challenges</span></p>
    </article>
  </section>

  <span class="ref-code">C60</span>
</main>
</body>
</html>
```